Maple Roster Business Card for recruitment company

We are looking for a Business Card Design that incorporates our personal details and our busines name and logo. We are a specialized search consultancy that recruit Property and Construction professionals.
We would like a business card that stands out and is appealing to the Construction and Property industry as well.

Target Market(s)

people in the construction and property industry

Contact Information for Business Card

Business Name and logo

Font styles to use
Serif

Colors
0094D4
00A9DD
6FCCEA
C7EBF8
E9F6FB

Requirements
Must have
• Business name and logo as well as contact details
Should not have
• No photos of us please

```html
<!DOCTYPE html>
<html lang="en">
<head>
<meta charset="utf-8">
<title>Maple Roster – Business Card</title>
<link rel="stylesheet" href="https://fonts.googleapis.com/css2?family=Cormorant+Garamond:wght@300;400&family=Lora:wght@400;500;700&display=swap">
<style>
  :root {
    --stage: #2b3036;
    --card: #0094d4;
    --card-deep: #0088c4;
    --ink: #ffffff;
    --rule: #c7ebf8;
    --soft: #6fccea;
    --band: #e9f6fb;
    --band-ink: #0094d4;
  }
  * { box-sizing: border-box; margin: 0; padding: 0; }
  html, body { width: 1200px; height: 780px; overflow: hidden; }
  body {
    background: var(--stage);
    font-family: "Lora", Georgia, serif;
    color: var(--ink);
    position: relative;
  }
  .card {
    position: absolute;
    top: 235px;
    width: 530px;
    height: 310px;
    background: linear-gradient(135deg, var(--card) 0%, var(--card-deep) 100%);
    border-radius: 18px;
    overflow: hidden;
    box-shadow: 0 18px 40px rgba(0,0,0,.45);
  }
  .card--front { left: 45px; }
  .card--back { left: 625px; }

  /* front */
  .brand-mark {
    position: absolute;
    left: 30px; top: 96px;
    width: 205px;
    display: flex; align-items: center; gap: 10px;
  }
  .brand-mark__dot {
    width: 18px; height: 18px; border-radius: 50%;
    background: var(--ink); flex: none;
  }
  .brand-mark__name {
    font-weight: 500; font-size: 24px; letter-spacing: .01em; line-height: 1.15;
    white-space: nowrap;
  }
  .divider {
    position: absolute; left: 248px; top: 110px;
    width: 1px; height: 175px; background: var(--rule);
  }
  .person {
    position: absolute; left: 270px; top: 90px; right: 0;
  }
  .person__name { font-weight: 700; font-size: 24px; letter-spacing: .02em; line-height: 1.2; }
  .person__title { font-weight: 400; font-size: 13px; letter-spacing: .05em; margin-top: 2px; color: var(--band); }
  .person__rule { height: 1px; background: var(--rule); margin-top: 6px; }
  .contacts {
    position: absolute; left: 270px; top: 170px; right: 16px;
    list-style: none; font-size: 14px; letter-spacing: .02em; line-height: 1.2;
  }
  .contacts li { display: flex; gap: 10px; align-items: flex-start; margin-bottom: 9px; white-space: nowrap; }
  .contacts svg { width: 14px; height: 14px; flex: none; margin-top: 1px; }

  /* back */
  .side-band {
    position: absolute; left: 0; top: 0; bottom: 0; width: 34px;
    background: var(--band);
  }
  .side-band__text {
    position: absolute; left: 17px; top: 50%;
    transform: translate(-50%, -50%) rotate(-90deg);
    white-space: nowrap; display: flex; align-items: center; gap: 7px;
    color: var(--band-ink); font-weight: 700; font-size: 13px; letter-spacing: .05em;
  }
  .side-band__text svg { width: 13px; height: 13px; }
  .wordmark {
    position: absolute; left: 34px; right: 0; top: 0; bottom: 0;
    display: flex; align-items: center; justify-content: center;
    font-family: "Cormorant Garamond", Georgia, serif;
    font-weight: 400; font-size: 52px; letter-spacing: .08em;
    white-space: nowrap;
  }
</style>
</head>
<body>
  <section class="card card--front" aria-label="Business card front">
    <div class="brand-mark">
      <span class="brand-mark__dot"></span>
      <span class="brand-mark__name">Maple Roster</span>
    </div>
    <div class="divider"></div>
    <div class="person">
      <h1 class="person__name">Daniel Hart</h1>
      <p class="person__title">General Manager</p>
      <div class="person__rule"></div>
    </div>
    <ul class="contacts">
      <li><svg viewBox="0 0 16 16" fill="none" stroke="#fff" stroke-width="1.3"><path d="M4 1.5l2.2 3-1.4 1.6a8 8 0 0 0 5 5l1.6-1.4 3 2.2-1.3 2.4C7.5 14.3 1.7 8.5 1.6 2.8z"/></svg>041-552-7390</li>
      <li><svg viewBox="0 0 16 16" fill="none" stroke="#fff" stroke-width="1.3"><rect x="1.5" y="3.5" width="13" height="9"/><path d="M1.5 3.5l6.5 5 6.5-5"/></svg>hello@mapleroster.com</li>
      <li><svg viewBox="0 0 16 16" fill="none" stroke="#fff" stroke-width="1.2"><circle cx="8" cy="8" r="6.5"/><ellipse cx="8" cy="8" rx="3" ry="6.5"/><path d="M1.5 8h13M2.5 4.8h11M2.5 11.2h11"/></svg>www.mapleroster.com</li>
      <li><svg viewBox="0 0 16 16" fill="none" stroke="#fff" stroke-width="1.3"><path d="M8 14.5s4.5-4.6 4.5-8a4.5 4.5 0 0 0-9 0c0 3.4 4.5 8 4.5 8z"/><circle cx="8" cy="6.3" r="1.6"/></svg><span>48 Example Road<br>Brookfield, 20415</span></li>
    </ul>
  </section>

  <section class="card card--back" aria-label="Business card back">
    <div class="side-band">
      <div class="side-band__text">
        <svg viewBox="0 0 16 16" fill="none" stroke="#0094d4" stroke-width="1.3"><circle cx="8" cy="8" r="6.5"/><ellipse cx="8" cy="8" rx="3" ry="6.5"/><path d="M1.5 8h13"/></svg>
        www.mapleroster.com
      </div>
    </div>
    <div class="wordmark">MAPLE ROSTER</div>
  </section>
</body>
</html>
```